Animal Eye Clinic needs a Business card

We are a new veterinary ophthalmology practice (Ridgeline Pet Vision Care) and we need a business card designed. We only see animal eyes - we are not a regular veterinary clinic. We already have a logo. We are looking for a professional, good looking business card to hand out to our clients. We are looking for something simple but professional and contemporary. Our logo is likely the only picture/graphic that needs to be on the card.
Updates

Contact Information for Business Card

Delia Vossman, BSc, DVM, MSc, DipACVO
Veterinary Ophthalmologist

Phone: 250.418.3927
Email: ridgelinepetvisioncare@mailbox-example.net
Website: ridgelinepetvisioncare-example.net
Address: 1874 Thornbury Rd
Kelowna, BC, V1X 4M9

Colors

Designer to choose colors to be used in the design.

Requirements
Must have
• Our logo (attached)

```html
<!DOCTYPE html>
<html lang="en">
<head>
<meta charset="utf-8">
<title>Ridgeline Pet Vision Care – Business Card</title>
<link href="https://fonts.googleapis.com/css2?family=Archivo:wght@400;500;700;800&display=swap" rel="stylesheet">
<style>
  :root {
    --stage: #3a3b3d;
    --card-dark: #2a2627;
    --card-light: #ffffff;
    --teal: #1a93a0;
    --ink: #1e1e1e;
    --paper-text: #f2f2f2;
  }
  * { margin: 0; padding: 0; box-sizing: border-box; }
  html, body {
    width: 1200px; height: 900px; overflow: hidden;
    background: var(--stage);
    font-family: "Archivo", Arial, sans-serif;
  }
  .canvas { position: relative; width: 1200px; height: 900px; }
  .card {
    position: absolute; width: 620px; height: 354px;
    box-shadow: 0 14px 30px rgba(0,0,0,.35);
  }
  .card--back { left: 90px; top: 80px; background: var(--card-dark); }
  .card--front { left: 490px; top: 466px; background: var(--card-light); }

  .brand { position: absolute; display: flex; align-items: center; gap: 10px; }
  .brand__dot { width: 22px; height: 22px; border-radius: 50%; background: var(--teal); flex: none; }
  .brand__name {
    color: var(--teal); font-weight: 800; text-transform: uppercase;
    line-height: 1.05; letter-spacing: .01em; white-space: nowrap;
  }
  .card--back .brand { left: 120px; top: 132px; }
  .card--back .brand__name { font-size: 27px; }
  .card--front .brand { left: 44px; top: 150px; }
  .card--front .brand__name { font-size: 18px; }

  .back__web {
    position: absolute; left: 300px; top: 238px;
    display: flex; align-items: center; gap: 8px;
    color: var(--paper-text); font-size: 14px;
  }
  .icon { width: 14px; height: 14px; flex: none; }

  .person { position: absolute; right: 34px; top: 34px; text-align: right; }
  .person__name { color: var(--teal); font-size: 27px; font-weight: 800; letter-spacing: .01em; text-transform: uppercase; }
  .person__cred, .person__role { color: var(--ink); font-size: 13px; line-height: 1.25; }

  .contacts { position: absolute; left: 290px; top: 190px; list-style: none; }
  .contacts li {
    display: flex; align-items: flex-start; gap: 10px;
    color: var(--ink); font-size: 13.5px; line-height: 1.3; margin-bottom: 6px;
    white-space: nowrap;
  }
  .contacts .icon { margin-top: 2px; }
</style>
</head>
<body>
<main class="canvas">

  <section class="card card--back" role="img" aria-label="Dark card back with a faint repeating brand-mark pattern">
    <div class="brand">
      <span class="brand__dot"></span>
      <span class="brand__name">Ridgeline<br>Pet Vision Care</span>
    </div>
    <p class="back__web">
      <svg class="icon" viewBox="0 0 14 14"><circle cx="7" cy="7" r="7" fill="#1a93a0"/><path d="M1 7h12M7 1c-3 3-3 9 0 12M7 1c3 3 3 9 0 12" stroke="#2a2627" stroke-width="1" fill="none"/></svg>
      ridgelinepetvisioncare-example.net
    </p>
  </section>

  <section class="card card--front">
    <div class="person">
      <h1 class="person__name">Delia Vossman</h1>
      <p class="person__cred">BSc, DVM, MSc, DipACVO</p>
      <p class="person__role">Veterinary Ophthalmologist</p>
    </div>

    <div class="brand">
      <span class="brand__dot"></span>
      <span class="brand__name">Ridgeline<br>Pet Vision Care</span>
    </div>

    <ul class="contacts">
      <li>
        <svg class="icon" viewBox="0 0 14 14"><path d="M3 1l2.5 3-1.5 1.5c.8 1.8 2 3 3.5 3.5L9 7.5l3 2.5-1.5 2.5C6 12.5 1.5 8 1.5 3.5z" fill="#1a93a0"/></svg>
        250.418.3927
      </li>
      <li>
        <svg class="icon" viewBox="0 0 14 14"><path d="M7 1a4 4 0 0 1 4 4c0 3-4 8-4 8S3 8 3 5a4 4 0 0 1 4-4z" fill="#1a93a0"/><circle cx="7" cy="5" r="1.5" fill="#fff"/></svg>
        <span>1874 Thornbury Rd,<br>Kelowna, BC, V1X 4M9</span>
      </li>
      <li>
        <svg class="icon" viewBox="0 0 14 14"><rect x="1" y="3" width="12" height="8.5" fill="#1a93a0"/><path d="M1 3l6 5 6-5" stroke="#fff" stroke-width="1.2" fill="none"/></svg>
        ridgelinepetvisioncare@mailbox-example.net
      </li>
      <li>
        <svg class="icon" viewBox="0 0 14 14"><circle cx="7" cy="7" r="6.3" fill="none" stroke="#1a93a0" stroke-width="1.3"/><path d="M1 7h12M7 1c-3 3-3 9 0 12M7 1c3 3 3 9 0 12" stroke="#1a93a0" stroke-width="1" fill="none"/></svg>
        ridgelinepetvisioncare-example.net
      </li>
    </ul>
  </section>

</main>
</body>
</html>
```